Corvane Paintless Dent Removal

Our company works on vehicles removing dents using a highly skilled trade which the metal is massaged out with special tools without disturbing the original paint, hence paintless dent removal. Besides keeping the paint and metal original its also very environmentally friendly since no paint or toxic fillers are used. Also we we are one of the most experienced companies in the business with 25 years

Target Market(s)

Retail Automobile consumers, Auto Dealerships and Auto Body Shops

Industry/Entity Type

Auto Repair

Contact Information for Business Card

Dale Hollister
PO Box 518 Brookmere, NY 11962
631-555-0148
corvanepdr@mailbox-example.com
website corvanepdr.example
youtube corvane paintless dent removal
25 years of experience removing Dents, Dings and Hail Damage

Font styles to use
Serif
Sans Serif

Colors

Designer to choose colors to be used in the design.

Requirements
Must have
• I do like things that are simple but classy and somewhat bold, also I like my logo so that should be somewhat important

```html
<!DOCTYPE html>
<html lang="en">
<head>
<meta charset="utf-8">
<title>Corvane Paintless Dent Removal – Business Card</title>
<link href="https://fonts.googleapis.com/css2?family=Roboto:wght@400;700;900&display=swap" rel="stylesheet">
<style>
  :root {
    --backdrop: #3b3b3d;
    --card: #232325;
    --brand-blue: #0b4f99;
    --brand-green: #7cc62a;
    --ink-light: #f2f2f2;
  }
  * { margin: 0; padding: 0; box-sizing: border-box; }
  html, body {
    width: 799px; height: 1200px; overflow: hidden;
    background: var(--backdrop);
    font-family: "Roboto", Arial, sans-serif;
  }
  .canvas {
    width: 799px; height: 1200px;
    display: flex; flex-direction: column; align-items: center; justify-content: space-around;
    padding: 60px 0;
  }
  .card {
    position: relative;
    width: 640px; height: 366px;
    background: var(--card);
    border-radius: 4px;
    box-shadow: 0 14px 30px rgba(0,0,0,.45);
    overflow: hidden;
  }
  /* Front */
  .card--front { display: flex; align-items: center; justify-content: center; }
  .brand-lockup { display: flex; align-items: center; gap: 18px; }
  .brand-dot { width: 22px; height: 22px; border-radius: 50%; background: var(--brand-blue); flex: none; }
  .brand-name {
    color: var(--brand-green);
    font-weight: 900;
    line-height: 1.05;
  }
  .brand-name .brand-main { display: block; font-size: 64px; letter-spacing: -1px; }
  .brand-name .brand-sub { display: block; font-size: 24px; }
  /* Back */
  .card--back { padding: 38px 44px; }
  .back-brand {
    color: var(--brand-blue);
    font-weight: 900;
    line-height: 1.05;
  }
  .back-brand .brand-main { display: block; font-size: 42px; letter-spacing: -1px; }
  .back-brand .brand-sub { display: block; font-size: 16px; }
  .person { margin-top: 30px; }
  .person-name { color: var(--brand-green); font-weight: 700; font-size: 26px; }
  .person-role { color: var(--ink-light); font-size: 14px; margin-top: 4px; }
  .contact { margin-top: 14px; color: var(--ink-light); font-size: 15px; line-height: 1.5; list-style: none; }
  .contact li { display: flex; align-items: center; gap: 10px; }
  .contact .address { padding-left: 0; }
  .contact svg { width: 14px; height: 14px; flex: none; fill: var(--brand-green); }
</style>
</head>
<body>
<main class="canvas">
  <section class="card card--front" aria-label="Business card front">
    <div class="brand-lockup">
      <span class="brand-dot"></span>
      <h1 class="brand-name">
        <span class="brand-main">CORVANE</span>
        <span class="brand-sub">Paintless Dent Removal</span>
      </h1>
    </div>
  </section>

  <section class="card card--back" aria-label="Business card back">
    <h2 class="back-brand">
      <span class="brand-main">CORVANE</span>
      <span class="brand-sub">Paintless Dent Removal</span>
    </h2>
    <div class="person">
      <p class="person-name">Dale Hollister</p>
      <p class="person-role">Managing Director</p>
    </div>
    <ul class="contact">
      <li class="address">PO Box 518 Brookmere, NY 11962</li>
      <li>
        <svg viewBox="0 0 24 24" aria-hidden="true"><path d="M6.6 10.8a15.1 15.1 0 0 0 6.6 6.6l2.2-2.2a1 1 0 0 1 1-.25 11.4 11.4 0 0 0 3.6.57 1 1 0 0 1 1 1V20a1 1 0 0 1-1 1A17 17 0 0 1 3 4a1 1 0 0 1 1-1h3.5a1 1 0 0 1 1 1c0 1.25.2 2.45.57 3.57a1 1 0 0 1-.25 1z"/></svg>
        631-555-0148
      </li>
      <li>
        <svg viewBox="0 0 24 24" aria-hidden="true"><path d="M2 5h20v14H2z M4 7v.5l8 5 8-5V7z" fill-rule="evenodd"/></svg>
        corvanepdr@mailbox-example.com
      </li>
      <li>
        <svg viewBox="0 0 24 24" aria-hidden="true"><path d="M12 2a10 10 0 1 0 0 20 10 10 0 0 0 0-20zm7.9 9h-3.4a15 15 0 0 0-1.4-6 8 8 0 0 1 4.8 6zM12 4c.9 1.3 2.2 3.8 2.5 7h-5C9.8 7.8 11.1 5.3 12 4zM4.1 13h3.4a15 15 0 0 0 1.4 6 8 8 0 0 1-4.8-6zm3.4-2H4.1a8 8 0 0 1 4.8-6 15 15 0 0 0-1.4 6zM12 20c-.9-1.3-2.2-3.8-2.5-7h5c-.3 3.2-1.6 5.7-2.5 7zm3.1-1a15 15 0 0 0 1.4-6h3.4a8 8 0 0 1-4.8 6z"/></svg>
        www.corvanepdr.example
      </li>
    </ul>
  </section>
</main>
</body>
</html>
```